Bref créative
Business cards, letter head, stationery
trial lawyer
Bright & Fun-filled
Tobias Whitfield
Trial Lawyer
2716 marlowe, suite 100
Corwin Falls Texas 77519
Pembrix@mailtorn.com
Need to include:
Offices in Harlow , Brennan Ridge, and Lamar Point Texas
Use winning logo

```html
<!DOCTYPE html>
<html lang="en">
<head>
<meta charset="utf-8">
<title>Tobias Whitfield — Stationery</title>
<link href="https://fonts.googleapis.com/css2?family=Cinzel:wght@600&family=Open+Sans:wght@400;600&display=swap" rel="stylesheet">
<style>
:root{
  --orange:#f07a1a;
  --orange-dark:#d9600b;
  --navy:#1f4a8c;
  --navy-dark:#163563;
  --paper:#ffffff;
  --ink:#4a4a4a;
  --muted:#8a8a8a;
  --bg:#e6e6e4;
}
*{margin:0;padding:0;box-sizing:border-box}
html,body{width:1200px;height:794px;overflow:hidden;background:var(--bg)}
body{position:relative;font-family:"Open Sans",sans-serif;color:var(--ink)}
.sheet{position:absolute;background:var(--paper);box-shadow:0 2px 8px rgba(0,0,0,.18);overflow:hidden}
.swoosh{position:absolute;right:0;bottom:0;width:100%;height:100%;pointer-events:none}

.brand{display:flex;align-items:center;gap:6px;position:relative;z-index:1}
.brand-mark{width:22px;height:22px;background:var(--orange);flex:none}
.brand-name{font-family:"Cinzel",serif;font-weight:600;color:var(--navy);font-size:13px;line-height:1.05;letter-spacing:.5px}
.brand-sub{font-family:"Open Sans",sans-serif;font-size:6px;color:var(--muted);letter-spacing:1px;margin-top:2px}

/* Letterhead */
.letterhead{left:40px;top:60px;width:470px;height:665px;padding:34px 40px}
.letterhead .brand-mark{width:28px;height:28px}
.letterhead .brand-name{font-size:16px}
.letter{margin-top:36px;font-size:8px;line-height:1.55;width:330px}
.letter p{margin-bottom:10px}
.recipient{margin-bottom:16px}
.signature{width:90px;height:26px;margin:6px 0;background:linear-gradient(90deg,#cfcfcf,#eee)}
.letter-footer{position:absolute;left:40px;bottom:22px;width:200px;font-size:6px;line-height:1.5;color:var(--muted);letter-spacing:.3px;z-index:1}

/* Envelope */
.envelope{left:550px;top:60px;width:390px;height:200px;padding:18px 20px}
.envelope-address{font-size:6px;color:var(--muted);margin-top:4px;line-height:1.5;position:relative;z-index:1}

/* Envelope backs */
.env-back{top:300px;width:120px;height:180px}
.env-back .flap{position:absolute;left:0;top:0;width:100%;height:55%}
.env-back .mark{position:absolute;left:50%;top:42%;width:22px;height:22px;margin-left:-11px;border:2px solid var(--paper)}
.back-white{left:550px}
.back-orange{left:685px}
.back-navy{left:820px}

/* Cards */
.card{left:980px;width:190px;height:108px;padding:14px 14px}
.card-offices{font-size:5.5px;letter-spacing:.4px;margin-top:10px;position:relative;z-index:1}
.card-contact{font-size:5.5px;line-height:1.5;margin-top:3px;position:relative;z-index:1}
.card-1{top:60px}
.card-2{top:185px;background:var(--orange)}
.card-3{top:310px;background:var(--navy)}
.card-4{top:435px}
.card-2 .brand-name,.card-3 .brand-name{color:var(--paper)}
.card-2 .brand-mark{background:var(--paper)}
.card-2 .brand-sub,.card-3 .brand-sub,.card-2 .card-offices,.card-3 .card-offices{color:var(--paper)}
.card-4 .card-name{font-size:8px;font-weight:600;color:var(--navy);position:absolute;right:16px;bottom:16px}
</style>
</head>
<body>

<section class="sheet letterhead">
  <div class="brand">
    <span class="brand-mark"></span>
    <div><div class="brand-name">Tobias Whitfield</div><div class="brand-sub">ATTORNEY AT LAW</div></div>
  </div>
  <div class="letter">
    <div class="recipient">Marian Holloway<br>48 Crestline Ave<br>Dalworth, Texas</div>
    <p>Dear Marian Holloway,</p>
    <p>Lorem ipsum dolor sit amet, consectetuer adipiscing elit, sed diam nonummy nibh euismod tincidunt ut laoreet dolore magna aliquam erat volutpat. Ut wisi enim ad minim veniam, quis nostrud exerci tation ullamcorper suscipit lobortis nisl ut aliquip ex ea commodo consequat. Duis autem vel eum iriure dolor in hendrerit in vulputate velit esse molestie consequat, vel illum dolore eu feugiat nulla facilisis at vero eros et accumsan et iusto odio dignissim qui blandit praesent luptatum zzril delenit augue duis dolore te feugait nulla facilisi.</p>
    <p>Lorem ipsum dolor sit amet, consectetuer adipiscing elit, sed diam nonummy nibh euismod tincidunt ut laoreet dolore magna aliquam erat volutpat. Ut wisi enim ad minim veniam, quis nostrud exerci tation ullamcorper suscipit lobortis nisl ut aliquip ex ea commodo consequat. Duis autem vel eum iriure dolor in hendrerit in vulputate velit esse molestie consequat.</p>
    <p>Duis autem vel eum iriure dolor in hendrerit in vulputate velit esse molestie consequat, vel illum dolore eu feugiat nulla facilisis at vero eros et accumsan et iusto odio dignissim qui blandit praesent luptatum zzril delenit augue duis dolore te feugait nulla facilisi.</p>
    <p>Sincerely,</p>
    <div class="signature" role="img" aria-label="Handwritten signature"></div>
    <div>Tobias Whitfield</div>
  </div>
  <div class="letter-footer">2716 marlowe, suite 100 · Corwin Falls Texas 77519<br>Pembrix@mailtorn.com · www.whitfieldtrial.com</div>
  <svg class="swoosh" viewBox="0 0 470 665" preserveAspectRatio="none">
    <path d="M470 470 C430 570 350 630 230 665 L470 665 Z" fill="var(--orange)"/>
    <path d="M470 540 C440 600 390 640 330 665 L470 665 Z" fill="var(--navy)"/>
  </svg>
</section>

<section class="sheet envelope">
  <div class="brand">
    <span class="brand-mark"></span>
    <div><div class="brand-name">Tobias Whitfield</div><div class="brand-sub">ATTORNEY AT LAW</div></div>
  </div>
  <div class="envelope-address">2716 marlowe, suite 100<br>Corwin Falls Texas 77519</div>
  <svg class="swoosh" viewBox="0 0 390 200" preserveAspectRatio="none">
    <path d="M390 60 C360 130 300 180 200 200 L390 200 Z" fill="var(--orange)"/>
    <path d="M390 120 C370 160 330 188 280 200 L390 200 Z" fill="var(--navy)"/>
  </svg>
</section>

<section class="sheet env-back back-white">
  <svg class="flap" viewBox="0 0 120 100" preserveAspectRatio="none"><path d="M0 0 L120 0 L60 100 Z" fill="#f4f4f4" stroke="#ddd"/></svg>
  <span class="mark" style="background:var(--orange)"></span>
</section>
<section class="sheet env-back back-orange">
  <svg class="flap" viewBox="0 0 120 100" preserveAspectRatio="none"><path d="M0 0 L120 0 L60 100 Z" fill="var(--orange)"/></svg>
  <span class="mark" style="background:var(--orange-dark)"></span>
</section>
<section class="sheet env-back back-navy">
  <svg class="flap" viewBox="0 0 120 100" preserveAspectRatio="none"><path d="M0 0 L120 0 L60 100 Z" fill="var(--navy)"/></svg>
  <span class="mark" style="background:var(--navy-dark)"></span>
</section>

<section class="sheet card card-1">
  <div class="brand">
    <span class="brand-mark"></span>
    <div><div class="brand-name">Tobias Whitfield</div><div class="brand-sub">ATTORNEY AT LAW</div></div>
  </div>
  <div class="card-offices">Harlow · Brennan Ridge · Lamar Point</div>
  <svg class="swoosh" viewBox="0 0 190 108" preserveAspectRatio="none">
    <path d="M0 92 C70 80 130 96 190 84 L190 108 L0 108 Z" fill="var(--orange)"/>
  </svg>
</section>

<section class="sheet card card-2">
  <div class="brand">
    <span class="brand-mark"></span>
    <div><div class="brand-name">Tobias Whitfield</div><div class="brand-sub">ATTORNEY AT LAW</div></div>
  </div>
  <div class="card-offices">Harlow · Brennan Ridge · Lamar Point</div>
  <svg class="swoosh" viewBox="0 0 190 108" preserveAspectRatio="none">
    <path d="M0 90 C70 78 130 94 190 82 L190 108 L0 108 Z" fill="var(--paper)"/>
  </svg>
</section>

<section class="sheet card card-3">
  <div class="brand">
    <span class="brand-mark"></span>
    <div><div class="brand-name">Tobias Whitfield</div><div class="brand-sub">ATTORNEY AT LAW</div></div>
  </div>
  <div class="card-offices">Harlow · Brennan Ridge · Lamar Point</div>
  <svg class="swoosh" viewBox="0 0 190 108" preserveAspectRatio="none">
    <path d="M0 92 C70 80 130 96 190 84 L190 108 L0 108 Z" fill="var(--orange)"/>
  </svg>
</section>

<section class="sheet card card-4">
  <div class="card-contact" style="margin-top:4px">2716 marlowe, suite 100<br>Corwin Falls Texas 77519<br>Pembrix@mailtorn.com</div>
  <div class="card-name">Tobias Whitfield</div>
  <svg class="swoosh" viewBox="0 0 190 108" preserveAspectRatio="none">
    <path d="M0 0 L190 0 L190 8 C120 20 60 4 0 14 Z" fill="var(--navy)"/>
  </svg>
</section>

</body>
</html>
```